Bright Pathway is a web based program in the sports industry. We are looking for a modern, cutting edge business card design. We are looking for a dark base and need to use three logo's on the card. Bright Pathway, Novafern Sports Supplements, and Ember Golf Academy.
Updates

This project is guaranteed. Not sure how to do that....

Industry/Entity Type

Business

Requirements
Must have
• 3 logo's... Bright Pathway... Ember Golf Academy... NovaFern Sports Supplements

```html
<!DOCTYPE html>
<html lang="en">
<head>
<meta charset="utf-8">
<title>Bright Pathway – Business Card</title>
<link rel="stylesheet" href="https://fonts.googleapis.com/css2?family=Roboto:wght@400;700;900&display=swap">
<style>
  :root {
    --orange: #f26522;
    --orange-deep: #e2561a;
    --white: #ffffff;
    --paper: #fbfbfb;
    --ink: #4a4a4a;
    --ink-soft: #7a7a7a;
    --red: #d91f26;
    --stage: #e9e9ea;
  }
  * { box-sizing: border-box; margin: 0; padding: 0; }
  html, body {
    width: 1200px; height: 900px; overflow: hidden;
    background: var(--stage);
    font-family: "Roboto", Arial, sans-serif;
  }
  .canvas {
    position: relative; width: 1200px; height: 900px;
  }
  .card {
    position: absolute; left: 320px; width: 560px; height: 320px;
    border-radius: 22px; overflow: hidden;
    box-shadow: 0 6px 18px rgba(0,0,0,0.18);
  }

  /* Front */
  .card-front { top: 100px; background: var(--orange); }
  .figure-area {
    position: absolute; right: 40px; top: 26px; width: 210px; height: 150px;
    border-radius: 40px;
    background: radial-gradient(ellipse at center, rgba(255,255,255,0.95) 0%, rgba(255,255,255,0.75) 55%, rgba(255,255,255,0) 72%);
  }
  .front-brand {
    position: absolute; left: 44px; top: 150px;
    display: flex; align-items: center; gap: 12px;
  }
  .brand-dot {
    width: 22px; height: 22px; border-radius: 50%; background: var(--white);
  }
  .front-brand .brand-name {
    color: var(--white); font-weight: 900; font-size: 44px; line-height: 0.95;
    letter-spacing: -0.5px;
  }
  .front-url {
    position: absolute; right: 34px; bottom: 26px;
    color: var(--white); font-weight: 700; font-size: 17px;
  }

  /* Back */
  .card-back { top: 480px; background: var(--paper); }
  .contact {
    position: absolute; left: 40px; top: 38px;
    color: var(--ink); font-size: 15px; line-height: 1.5;
  }
  .contact .label { color: var(--ink-soft); }
  .person {
    position: absolute; left: 40px; bottom: 38px;
  }
  .person-name {
    color: var(--orange); font-size: 30px; font-weight: 400;
  }
  .person-phone {
    color: var(--ink); font-size: 17px; margin-top: 4px; letter-spacing: 0.5px;
  }
  .partners {
    position: absolute; right: 0; top: 0; bottom: 0; width: 190px;
    border-left: 1px solid #e3e3e3;
    display: flex; flex-direction: column; justify-content: space-around;
    padding: 26px 22px;
  }
  .partner {
    display: flex; align-items: center; gap: 10px;
    font-weight: 700; font-size: 14px; line-height: 1.15; color: var(--ink);
  }
  .partner-mark-circle { width: 26px; height: 26px; border-radius: 50%; background: var(--red); flex: none; }
  .partner-mark-square { width: 24px; height: 24px; background: var(--red); flex: none; }
  .partner-mark-dot { width: 20px; height: 20px; border-radius: 50%; background: var(--orange); flex: none; }
  .partner-home { color: var(--orange); font-size: 18px; font-weight: 900; }
</style>
</head>
<body>
<main class="canvas">
  <section class="card card-front" aria-label="Business card front">
    <div class="figure-area" role="img" aria-label="White silhouette of an athlete kicking a ball"></div>
    <div class="front-brand">
      <span class="brand-dot"></span>
      <span class="brand-name">Bright<br>Pathway</span>
    </div>
    <p class="front-url">www.brightpathway.com</p>
  </section>

  <section class="card card-back" aria-label="Business card back">
    <address class="contact">
      2240 Meadow Crest Way<br>
      Lakeview, FL 30012<br>
      <span class="label">e:</span> dan@brightpathway.com<br>
      <span class="label">w:</span> www.brightpathway.com<br>
      <span class="label">twitter:</span> @BrightPathway
    </address>
    <div class="person">
      <p class="person-name">Dan Harlow</p>
      <p class="person-phone">555-014-2236</p>
    </div>
    <div class="partners">
      <div class="partner"><span class="partner-mark-circle"></span><span>Ember Golf<br>Academy</span></div>
      <div class="partner"><span class="partner-mark-square"></span><span>NovaFern Sports<br>Supplements</span></div>
      <div class="partner partner-home"><span class="partner-mark-dot"></span><span>Bright<br>Pathway</span></div>
    </div>
  </section>
</main>
</body>
</html>
```